Pitch Deck presentation

Design multiple graphics and slides that can be used in a PowerPoint presentation.
4 infographics, text templates and blank templates
Attached you will find the infographics references and a couple of styles we would like to have on the presentations
We prefer a simpler design with not too much background noise or colors(prefer to have whiter backgrounds)
The infographics in the whiteboard should be presented 1 per slide with space on the right side to write text for explanation.
4 total columns will be the equivalent to the 4 different slides with design in the presentation.
Attached you have our colors and logos.
https://files.plomvarek.net/share/7qKtr2WnZe4xBvLp9HsD3aYuM0cFgR?mode=view
You can reach out to me with any questions at my email mkestrubio@hallowpine.com

```html
<!DOCTYPE html>
<html lang="en">
<head>
<meta charset="utf-8">
<title>Routewise Freight — Pitch Deck Slides</title>
<link href="https://fonts.googleapis.com/css2?family=Nunito:wght@300;400;700;800;900&family=Lato:wght@400;700&display=swap" rel="stylesheet">
<style>
:root{
  --orange:#e24e1b;
  --orange-deep:#d8461a;
  --ink:#2b2b2b;
  --dark:#333335;
  --grey-bg:#a4a4a4;
  --card:#f3f3f4;
  --muted:#555;
  --white:#fff;
}
*{box-sizing:border-box;margin:0;padding:0}
html,body{width:1026px;height:1200px;overflow:hidden}
body{background:var(--grey-bg);font-family:'Lato',sans-serif;color:var(--ink);position:relative}
.slide{position:absolute;width:444px;height:249px;background:var(--white);overflow:hidden;box-shadow:0 6px 14px rgba(0,0,0,.25)}
.col-a{left:51px}.col-b{left:531px}
.row-1{top:54px}.row-2{top:335px}.row-3{top:616px}.row-4{top:897px}
.abs{position:absolute}
.brand{position:absolute;right:25px;top:10px;font-family:'Nunito',sans-serif;font-weight:900;font-size:15px;letter-spacing:.5px;color:var(--ink);line-height:1;text-align:right}
.brand.light{color:var(--white)}
.slide-title{position:absolute;left:25px;top:15px;font-family:'Nunito',sans-serif;font-size:12.5px;font-weight:300;letter-spacing:.3px;color:var(--ink)}
.slide-title b{font-weight:800}
.title-rule{position:absolute;left:0;top:38px;width:84px;height:1.5px;background:var(--orange)}
.title-rule::after{content:"";position:absolute;right:-4px;top:-3.3px;width:8px;height:8px;border-radius:50%;background:var(--orange)}
.footer-rule{position:absolute;left:0;top:237px;width:241px;height:.6px;background:#cfcfcf}
.footer-call{position:absolute;left:258px;top:233px;font-size:5.6px;font-weight:700;color:var(--ink);display:flex;align-items:center;gap:4px}
.footer-call svg{width:5px;height:5px}
.page-no{position:absolute;left:404px;top:231px;width:12px;height:12px;background:var(--orange);transform:rotate(45deg)}
.page-no span{position:absolute;inset:0;transform:rotate(-45deg);display:flex;align-items:center;justify-content:center;color:#fff;font-size:5px;font-weight:700}
.on-orange .footer-rule{background:rgba(255,255,255,.5)}
.on-orange .footer-call{color:#fff}
.on-orange .page-no{background:#fff}
.on-orange .page-no span{color:var(--orange)}
.on-dark .footer-call{color:#fff}
.on-dark .footer-rule{background:#666}
.icon-ring{position:absolute;border-radius:50%;border:2.2px solid var(--orange);background:#fff;display:flex;align-items:center;justify-content:center}
.icon-dot{position:absolute;border-radius:50%;display:flex;align-items:center;justify-content:center}
.icon-dot.dark{background:var(--dark)}
.icon-dot.orange{background:var(--orange)}
.photo{position:absolute}
/* cover */
.cover-photo{left:0;top:0;width:444px;height:191px;background:linear-gradient(180deg,#8d8d8d 0%,#5f5f5f 55%,#3c3c3c 100%)}
.cover-name{position:absolute;left:0;right:0;top:62px;text-align:center;font-family:'Nunito',sans-serif;font-weight:900;font-size:38px;color:#fff;letter-spacing:1px}
.cover-band{position:absolute;left:0;top:194px;width:444px;height:2px;background:var(--orange)}
.cover-tag{position:absolute;left:0;right:0;top:208px;text-align:center;font-family:'Nunito',sans-serif;font-weight:900;font-size:13.5px;line-height:17px;color:var(--ink)}
.cover-tag em{font-style:normal;color:var(--orange)}
/* text */
.lead{font-size:6.3px;line-height:9px;font-weight:700;color:var(--ink)}
.item-head{font-size:6.8px;font-weight:700;color:var(--ink);margin-bottom:3px}
.item-body{font-size:5.2px;line-height:8.3px;color:var(--muted)}
.card{position:absolute;top:66px;width:122px;height:142px;background:var(--card);border-radius:6px}
.card h3{position:absolute;left:10px;top:60px;font-size:10px;font-weight:700;color:var(--ink)}
.card p{position:absolute;left:10px;top:78px;width:104px;font-size:6px;line-height:9.2px;color:#444}
.bullet-block{position:absolute}
.bullet-block h4{font-size:6px;font-weight:700;color:var(--ink);margin-bottom:2px}
.bullet-block ul{list-style:none}
.bullet-block li{font-size:4.7px;line-height:7.4px;color:#444;padding-left:6px;position:relative}
.bullet-block li::before{content:"";position:absolute;left:0;top:2.6px;width:2.2px;height:2.2px;border-radius:50%;background:var(--orange)}
.feature-list{position:absolute;top:58px;width:185px;list-style:none}
.feature-list li{font-size:4.9px;line-height:8.6px;color:#444;padding-left:12px;position:relative;margin-bottom:5.5px}
.feature-list li::before{content:"";position:absolute;left:0;top:2px;width:3.5px;height:3.5px;border-radius:50%;border:1.2px solid var(--orange)}
.divider-bg{background:linear-gradient(135deg,var(--orange) 0%,var(--orange-deep) 100%)}
.divider-title{position:absolute;left:0;right:0;top:110px;text-align:center;font-family:'Nunito',sans-serif;font-size:27px;color:#fff;font-weight:400;letter-spacing:.5px}
.divider-title b{font-weight:900}
.thanks-title{position:absolute;left:238px;top:77px;font-family:'Nunito',sans-serif;font-size:18px;font-weight:300;color:#fff}
.thanks-title b{font-weight:900}
.thanks-sub{position:absolute;left:238px;top:124px;width:190px;font-family:'Nunito',sans-serif;font-size:9.2px;line-height:12.5px;color:#fff}
.social{position:absolute;top:155px;width:14px;height:14px;border-radius:50%;border:1px solid var(--orange)}
</style>
</head>
<body>

<!-- Slide 1: cover -->
<section class="slide col-a row-1">
  <div class="photo cover-photo" role="img" aria-label="Black and white photo of a semi truck driving on a desert highway"></div>
  <div class="cover-name">ROUTEWISE</div>
  <div class="cover-band"></div>
  <p class="cover-tag">SUPERIOR SERVICE, <em>COMPLETE</em><br><em>TRANSPARENCY</em></p>
</section>

<!-- Slide 2: mission -->
<section class="slide col-b row-1">
  <svg class="abs" style="left:0;top:0" width="444" height="249" viewBox="0 0 444 249">
    <polygon points="264,0 270,0 305,225 299,225" fill="var(--orange)"/>
  </svg>
  <div class="photo" style="left:0;top:0;width:444px;height:225px;clip-path:polygon(272px 0,444px 0,444px 225px,306px 225px);background:linear-gradient(180deg,#8a8a8a,#4d4d4d)" role="img" aria-label="Smiling woman with crossed arms in front of a row of trucks"></div>
  <div class="brand light">ROUTEWISE</div>
  <h2 class="slide-title"><b>ROUTEWISE</b> MISSION</h2>
  <div class="title-rule"></div>
  <p class="abs lead" style="left:25px;top:59px;width:245px">Routewise's Mission is to reintroduce Freedom in the freight industry by providing a sustainable Free Market solution through moral Innovation.</p>

  <div class="icon-ring" style="left:25px;top:90px;width:33px;height:33px">
    <svg width="15" height="15" viewBox="0 0 16 16" fill="var(--ink)"><rect x="2" y="9" width="4" height="6"/><rect x="7" y="6" width="4" height="9"/><circle cx="12" cy="3" r="2"/></svg>
  </div>
  <div class="abs" style="left:70px;top:89px;width:200px">
    <div class="item-head">FOR FREEDOM</div>
    <p class="item-body">We believe in challenging the system that limits our choices and find it our duty to pioneer the path to restore America to her rightful place where the quality of our success grows with each interaction.</p>
  </div>

  <div class="icon-ring" style="left:25px;top:135px;width:33px;height:33px">
    <svg width="14" height="14" viewBox="0 0 16 16"><circle cx="8" cy="8" r="6.5" fill="var(--ink)"/><path d="M8 8 L8 1.5 A6.5 6.5 0 0 1 14.5 8 Z" fill="#fff"/></svg>
  </div>
  <div class="abs" style="left:70px;top:134px;width:200px">
    <div class="item-head">A FREE MARKET SOLUTION</div>
    <p class="item-body">Freedom is created for the freight industry through a new system of stable voluntary exchanges where interactions are honest and transparent, creating ever expanding opportunities for both shippers and carriers.</p>
  </div>

  <div class="icon-ring" style="left:25px;top:180px;width:33px;height:33px">
    <svg width="13" height="14" viewBox="0 0 16 16" fill="var(--ink)"><circle cx="8" cy="6" r="5"/><rect x="6" y="11" width="4" height="3"/></svg>
  </div>
  <div class="abs" style="left:70px;top:179px;width:200px">
    <div class="item-head">THROUGH INNOVATION</div>
    <p class="item-body">Through the power of next generation computing and communication, Routewise has created a place where shippers and carriers can interact in an open and safe environment.</p>
  </div>

  <div class="footer-rule"></div>
  <div class="footer-call"><svg viewBox="0 0 10 10"><path d="M2 0l2 2-1 2 3 3 2-1 2 2-2 2C4 10 0 6 0 2z" fill="var(--orange)"/></svg>Have a question? Give us a call! 555-014-2286</div>
  <div class="page-no"><span>02</span></div>
</section>

<!-- Slide 3: vision -->
<section class="slide col-a row-2">
  <div class="brand">ROUTEWISE</div>
  <h2 class="slide-title"><b>ROUTEWISE</b> VISION</h2>
  <div class="title-rule"></div>

  <div class="card" style="left:25px">
    <div class="icon-ring" style="left:10px;top:12px;width:36px;height:36px"><svg width="16" height="14" viewBox="0 0 16 14" fill="var(--ink)"><rect x="0" y="3" width="11" height="8" rx="2"/><circle cx="12" cy="4" r="4"/></svg></div>
    <h3>Why?</h3>
    <p>Today's shipper and carrier relationship is mismanaged, causing a lack of visibility and reliability for both parties.</p>
  </div>
  <div class="card" style="left:161px">
    <div class="icon-ring" style="left:10px;top:12px;width:36px;height:36px"><svg width="16" height="16" viewBox="0 0 16 16"><circle cx="8" cy="8" r="7.5" fill="var(--ink)"/><text x="8" y="11.5" font-size="10" font-weight="700" text-anchor="middle" fill="#fff" font-family="Lato,sans-serif">?</text></svg></div>
    <h3>What?</h3>
    <p>Routewise reinvents the shipper and carrier relationship through a specialized process and custom technology designed specifically to address the areas the freight industry ignores.</p>
  </div>
  <div class="card" style="left:296px">
    <div class="icon-ring" style="left:10px;top:12px;width:36px;height:36px"><svg width="12" height="16" viewBox="0 0 12 16" fill="var(--ink)"><circle cx="6" cy="6" r="5"/><rect x="3" y="11" width="6" height="4"/></svg></div>
    <h3>How?</h3>
    <p>Our unparalleled transparency, superior service, and innovative process allow organizations to gain a deep visibility into their logistics operations.</p>
  </div>

  <div class="footer-rule"></div>
  <div class="footer-call"><svg viewBox="0 0 10 10"><path d="M2 0l2 2-1 2 3 3 2-1 2 2-2 2C4 10 0 6 0 2z" fill="var(--orange)"/></svg>Have a question? Give us a call! 555-014-2286</div>
  <div class="page-no"><span>03</span></div>
</section>

<!-- Slide 4: section divider -->
<section class="slide col-b row-2 on-orange divider-bg">
  <div class="brand light">ROUTEWISE</div>
  <h2 class="divider-title"><b>SECTION</b> DIVIDER</h2>
  <div class="footer-rule"></div>
  <div class="footer-call"><svg viewBox="0 0 10 10"><path d="M2 0l2 2-1 2 3 3 2-1 2 2-2 2C4 10 0 6 0 2z" fill="#fff"/></svg>Have a question? Give us a call! 555-014-2286</div>
  <div class="page-no"><span>04</span></div>
</section>

<!-- Slide 5: shippers -->
<section class="slide col-a row-3">
  <div class="brand">ROUTEWISE</div>
  <h2 class="slide-title"><b>OUR</b> SHIPPERS</h2>
  <div class="title-rule"></div>
  <svg class="abs" style="left:0;top:0" width="444" height="249" viewBox="0 0 444 249">
    <circle cx="135" cy="144" r="75" fill="none" stroke="#555" stroke-width=".8" stroke-dasharray="3 2"/>
    <circle cx="135" cy="144" r="60" fill="#fff" style="filter:drop-shadow(0 3px 6px rgba(0,0,0,.15))"/>
    <circle cx="188" cy="91" r="2.3" fill="#fff" stroke="var(--ink)" stroke-width="1"/>
    <circle cx="206" cy="120" r="2.3" fill="#fff" stroke="var(--orange)" stroke-width="1"/>
    <circle cx="209" cy="152" r="2.3" fill="#fff" stroke="var(--ink)" stroke-width="1"/>
    <circle cx="193" cy="191" r="2.3" fill="#fff" stroke="var(--orange)" stroke-width="1"/>
  </svg>
  <div class="abs" style="left:75px;top:136px;width:120px;text-align:center;font-family:'Nunito',sans-serif;font-weight:900;font-size:15px;color:var(--ink)">ROUTEWISE</div>

  <div class="icon-dot dark" style="left:197px;top:58px;width:31px;height:31px"><svg width="13" height="11" viewBox="0 0 14 11" fill="#fff"><rect x="0" y="0" width="14" height="9" rx="1"/><rect x="3" y="9" width="8" height="2"/></svg></div>
  <div class="icon-dot orange" style="left:218px;top:102px;width:31px;height:31px"><svg width="14" height="12" viewBox="0 0 16 14" fill="#fff"><rect x="0" y="3" width="11" height="8" rx="2"/><circle cx="12" cy="4" r="4"/></svg></div>
  <div class="icon-dot dark" style="left:218px;top:146px;width:31px;height:31px"><svg width="13" height="12" viewBox="0 0 14 12" fill="#fff"><rect x="2" y="0" width="10" height="6" rx="1"/><circle cx="4" cy="8" r="2"/><circle cx="10" cy="8" r="2"/></svg></div>
  <div class="icon-dot orange" style="left:197px;top:189px;width:31px;height:31px"><svg width="13" height="12" viewBox="0 0 14 12" fill="#fff"><rect x="7" y="2" width="2" height="5"/><rect x="10" y="0" width="2" height="7"/><circle cx="4" cy="4" r="2"/><rect x="1" y="8" width="12" height="4" rx="2"/></svg></div>

  <div class="bullet-block" style="left:238px;top:55px">
    <h4>LOREM IPSUM DOLOR</h4>
    <ul><li>Lorem ipsum dolor sit amet, consectetur adipiscing</li><li>Elit, sed do eiusmod tempor incididunt</li><li>Lorem ipsum dolor sit amet, consectetur adipiscing</li><li>Elit, sed do eiusmod tempor incididunt</li></ul>
  </div>
  <div class="bullet-block" style="left:259px;top:105px">
    <h4>LOREM IPSUM DOLOR</h4>
    <ul><li>Lorem ipsum dolor sit amet, consectetur adipiscing</li><li>Elit, sed do eiusmod tempor incididunt</li></ul>
  </div>
  <div class="bullet-block" style="left:259px;top:149px">
    <h4>LOREM IPSUM DOLOR</h4>
    <ul><li>Lorem ipsum dolor sit amet, consectetur adipiscing</li><li>Elit, sed do eiusmod tempor incididunt</li></ul>
  </div>
  <div class="bullet-block" style="left:238px;top:191px">
    <h4>LOREM IPSUM DOLOR</h4>
    <ul><li>Lorem ipsum dolor sit amet, consectetur adipiscing</li><li>Elit, sed do eiusmod tempor incididunt</li><li>Lorem ipsum dolor sit amet, consectetur adipiscing</li></ul>
  </div>

  <div class="footer-rule"></div>
  <div class="footer-call"><svg viewBox="0 0 10 10"><path d="M2 0l2 2-1 2 3 3 2-1 2 2-2 2C4 10 0 6 0 2z" fill="var(--orange)"/></svg>Have a question? Give us a call! 555-014-2286</div>
  <div class="page-no"><span>05</span></div>
</section>

<!-- Slide 6: carriers -->
<section class="slide col-b row-3">
  <div class="brand">ROUTEWISE</div>
  <h2 class="slide-title"><b>OUR</b> CARRIERS</h2>
  <div class="title-rule"></div>
  <svg class="abs" style="left:0;top:0" width="444" height="249" viewBox="0 0 444 249">
    <circle cx="124" cy="138" r="80" fill="var(--orange)"/>
    <path d="M212 58 C260 100 260 180 212 218" fill="none" stroke="#555" stroke-width=".7" stroke-dasharray="2 2"/>
    <circle cx="212" cy="58" r="1.4" fill="#555"/><circle cx="212" cy="218" r="1.4" fill="#555"/>
  </svg>
  <div class="photo" style="left:63px;top:71px;width:134px;height:134px;border-radius:50%;background:radial-gradient(circle at 55% 40%,#b8a77a,#5d6a4e 70%,#3c3f3a)" role="img" aria-label="Smiling truck driver with crossed arms in front of a shipping container"></div>

  <div class="icon-dot dark" style="left:218px;top:75px;width:31px;height:31px;box-shadow:0 2px 5px rgba(0,0,0,.3)"><svg width="12" height="13" viewBox="0 0 12 13" fill="#fff"><rect x="1" y="0" width="10" height="9" rx="1"/><rect x="0" y="9" width="12" height="2"/><circle cx="3" cy="12" r="1"/><circle cx="9" cy="12" r="1"/></svg></div>
  <div class="icon-dot orange" style="left:230px;top:124px;width:31px;height:31px;box-shadow:0 2px 5px rgba(0,0,0,.3)"><svg width="12" height="13" viewBox="0 0 12 13" fill="#fff"><circle cx="6" cy="4" r="3.5"/><rect x="1" y="8" width="10" height="5" rx="2"/></svg></div>
  <div class="icon-dot dark" style="left:218px;top:172px;width:31px;height:31px;box-shadow:0 2px 5px rgba(0,0,0,.3)"><svg width="13" height="12" viewBox="0 0 13 12" fill="#fff"><circle cx="6.5" cy="4" r="3"/><path d="M0 6l4 6h5l4-6-2 0-3 3H5L2 6z"/></svg></div>

  <div class="bullet-block" style="left:262px;top:74px">
    <h4>LOREM IPSUM DOLOR</h4>
    <ul><li>Lorem ipsum dolor sit amet, consectetur adipiscing</li><li>Elit, sed do eiusmod tempor incididunt</li><li>Lorem ipsum dolor sit amet, consectetur adipiscing</li></ul>
  </div>
  <div class="bullet-block" style="left:274px;top:122px">
    <h4>LOREM IPSUM DOLOR</h4>
    <ul><li>Lorem ipsum dolor sit amet, consectetur adipiscing</li><li>Elit, sed do eiusmod tempor incididunt</li><li>Lorem ipsum dolor sit amet, consectetur adipiscing</li></ul>
  </div>
  <div class="bullet-block" style="left:262px;top:171px">
    <h4>LOREM IPSUM DOLOR</h4>
    <ul><li>Lorem ipsum dolor sit amet, consectetur adipiscing</li><li>Elit, sed do eiusmod tempor incididunt</li><li>Lorem ipsum dolor sit amet, consectetur adipiscing</li></ul>
  </div>

  <div class="footer-rule"></div>
  <div class="footer-call"><svg viewBox="0 0 10 10"><path d="M2 0l2 2-1 2 3 3 2-1 2 2-2 2C4 10 0 6 0 2z" fill="var(--orange)"/></svg>Have a question? Give us a call! 555-014-2286</div>
  <div class="page-no"><span>06</span></div>
</section>

<!-- Slide 7: features -->
<section class="slide col-a row-4">
  <div class="brand">ROUTEWISE</div>
  <h2 class="slide-title"><b>OUR</b> FEATURES</h2>
  <div class="title-rule"></div>
  <ul class="feature-list" style="left:25px">
    <li>Lorem ipsum dolor sit amet, consectetur adipiscing elit, sed do eiusmod tempor incididunt ut labore et dolore magna aliqua. Ut enim ad minim veniam, quis nostrud exercitation ullamco laboris nisi ut aliquip ex ea commodo consequat.</li>
    <li>Lorem ipsum dolor sit amet, consectetur adipiscing elit, sed do eiusmod tempor incididunt ut labore et dolore magna aliqua. Ut enim ad minim veniam, quis nostrud exercitationea.</li>
    <li>Lorem ipsum dolor sit amet, consectetur adipiscing elit, sed do eiusmod tempor incididunt ut labore et dolore magna aliqua. Ut enim ad minim veniam, quis nostrud exercitation ullamco laboris nisi ut aliquip ex ea commodo consequat.</li>
    <li>Lorem ipsum dolor sit amet, consectetur adipiscing elit, sed do eiusmod tempor incididunt ut labore et dolore magna aliqua. Ut enim ad minim veniam, quis nostrud exercitationea.</li>
    <li>Lorem ipsum dolor sit amet, consectetur adipiscing elit, sed do eiusmod tempor incididunt ut labore et dolore magna aliquaea.</li>
  </ul>
  <ul class="feature-list" style="left:234px">
    <li>Lorem ipsum dolor sit amet, consectetur adipiscing elit, sed do eiusmod tempor incididunt ut labore et dolore magna aliqua. Ut enim ad minim veniam, quis nostrud exercitation ullamco laboris nisi ut aliquip ex ea commodo consequat.</li>
    <li>Lorem ipsum dolor sit amet, consectetur adipiscing elit, sed do eiusmod tempor incididunt ut labore et dolore magna aliqua. Ut enim ad minim veniam, quis nostrud exercitationea.</li>
    <li>Lorem ipsum dolor sit amet, consectetur adipiscing elit, sed do eiusmod tempor incididunt ut labore et dolore magna aliqua. Ut enim ad minim veniam, quis nostrud exercitation ullamco laboris nisi ut aliquip ex ea commodo consequat.</li>
    <li>Lorem ipsum dolor sit amet, consectetur adipiscing elit, sed do eiusmod tempor incididunt ut labore et dolore magna aliqua. Ut enim ad minim veniam, quis nostrud exercitationea.</li>
    <li>Lorem ipsum dolor sit amet, consectetur adipiscing elit, sed do eiusmod tempor incididunt ut labore et dolore magna aliquaea.</li>
  </ul>
  <div class="footer-rule"></div>
  <div class="footer-call"><svg viewBox="0 0 10 10"><path d="M2 0l2 2-1 2 3 3 2-1 2 2-2 2C4 10 0 6 0 2z" fill="var(--orange)"/></svg>Have a question? Give us a call! 555-014-2286</div>
  <div class="page-no"><span>07</span></div>
</section>

<!-- Slide 8: thank you -->
<section class="slide col-b row-4 on-dark" style="background:var(--dark)">
  <svg class="abs" style="left:0;top:0" width="444" height="249" viewBox="0 0 444 249">
    <polygon points="0,0 220,0 222,150 72,225 0,225" fill="var(--orange)"/>
  </svg>
  <div class="photo" style="left:0;top:0;width:444px;height:249px;clip-path:polygon(0 0,216px 0,218px 148px,70px 222px,0 222px);background:linear-gradient(160deg,#9a9a9a,#5c5c5c 60%,#3d3d3d)" role="img" aria-label="Black and white photo of a semi truck in front of mountains"></div>
  <div class="brand light">ROUTEWISE</div>
  <h2 class="thanks-title"><b>THANK</b> YOU</h2>
  <div class="abs" style="left:223px;top:105px;width:40px;height:1.5px;background:var(--orange)"></div>
  <div class="abs" style="left:259px;top:102px;width:8px;height:8px;border-radius:50%;background:var(--orange)"></div>
  <p class="thanks-sub">Your Comprehensive Freight Management Solution</p>
  <span class="social" style="left:238px"></span>
  <span class="social" style="left:256px"></span>
  <span class="social" style="left:274px"></span>
  <span class="social" style="left:292px"></span>
  <div class="footer-rule"></div>
  <div class="footer-call"><svg viewBox="0 0 10 10"><path d="M2 0l2 2-1 2 3 3 2-1 2 2-2 2C4 10 0 6 0 2z" fill="var(--orange)"/></svg>Have a question? Give us a call! 555-014-2286</div>
  <div class="page-no"><span>08</span></div>
</section>

</body>
</html>
```